New website for actress www.miriam-halvorsen.de

My website is a little old and needs a new look.
I am a german actress who is in the TV and Theaterbusiness.
my twitter account is called MirHalvorsen
this design will be set up as wordpress site and needs to be optimized for mobile,
so please provide mobile screen views too.
the content will not change much from the excisting site but I would like to have a news section with Videos and press Releases
I would also like my Chatter Feed to be displayed on my landing page.
I am looking forward to your ideas
best regards
miriam

Target Market(s)

press and fans

Industry/Entity Type

Tv

Font styles to use
Serif
Sans Serif

Colors

Designer to choose colors to be used in the design.

Requirements
Must have
• see above

```html
<!DOCTYPE html>
<html lang="de">
<head>
<meta charset="utf-8">
<title>Miriam Halvorsen</title>
<link href="https://fonts.googleapis.com/css2?family=Open+Sans:wght@300;400;600;700&display=swap" rel="stylesheet">
<style>
:root{
  --pink:#ef5f9f;
  --pink-deep:#e0267f;
  --purple:#6b2f93;
  --purple-soft:#7a3aa3;
  --text:#555;
  --text-light:#777;
  --line:#e6e6e6;
  --white:#fff;
}
*{margin:0;padding:0;box-sizing:border-box}
html,body{width:910px;height:1200px;overflow:hidden;background:var(--white)}
body{font-family:"Open Sans",Arial,sans-serif;color:var(--text);position:relative}
.top-stripe{position:absolute;left:0;top:0;width:910px;height:4px;
  background:linear-gradient(90deg,#f49ac1 0 12.5%,var(--pink) 12.5% 25%,#e85597 25% 37.5%,var(--purple) 37.5% 50%,#f49ac1 50% 62.5%,var(--pink) 62.5% 75%,#e0267f 75% 87.5%,#9c6bc4 87.5% 100%)}
.brand{position:absolute;top:26px;width:910px;text-align:center}
.brand-name{font-size:34px;font-weight:600;letter-spacing:.2px;line-height:1.1}
.brand-name .first{color:var(--purple)}
.brand-name .last{color:var(--pink-deep)}
.brand-slogan{font-size:14px;font-weight:300;color:var(--pink-deep);margin-top:1px}
.main-nav{position:absolute;top:98px;left:0;width:910px;height:44px;background:var(--pink);display:flex;padding-left:34px}
.main-nav a{color:var(--white);text-decoration:none;font-size:13.5px;line-height:44px;padding:0 14px;border-right:1px solid rgba(255,255,255,.25)}
.main-nav a:first-child{padding-left:14px}
.main-nav a:last-child{border-right:none}
.hero{position:absolute;top:142px;left:0;width:910px;height:354px;overflow:hidden;
  background:linear-gradient(90deg,#fbfbfb 0%,#f2f2f3 40%,#e7e4ec 55%,#d9c49a 68%,#c9a46b 78%,#9a8c7a 92%,#6f6a5e 100%)}
.hero-fade{position:absolute;inset:0;background:linear-gradient(90deg,#fff 0%,rgba(255,255,255,.85) 35%,rgba(255,255,255,0) 60%)}
.hero-text{position:absolute;left:56px;top:86px}
.hero-kicker{font-size:28px;color:var(--purple);font-weight:400;line-height:1.1}
.hero-title{font-size:36px;color:var(--pink-deep);font-weight:700;line-height:1.2}
.hero-copy{font-size:11.5px;color:var(--text-light);line-height:18px;margin-top:6px;width:360px}
.dots{display:flex;gap:3px;margin-top:14px}
.dots span{width:10px;height:10px;border-radius:50%;background:#d6d6d6}
.dots span.active{background:var(--purple)}
.intro{position:absolute;left:45px;top:525px;width:560px}
.intro h1{font-size:28px;font-weight:300;color:#333;line-height:1.2}
.intro h2{font-size:20px;font-weight:300;color:#333;margin:4px 0 10px}
.intro p{font-size:11px;line-height:17.6px;color:var(--text-light);margin:0 0 8px 3px}
.feed{position:absolute;left:628px;top:520px;width:238px;height:298px;border:1px solid var(--line);border-radius:3px}
.feed-head{background:var(--purple-soft);color:var(--white);font-size:18px;height:38px;line-height:38px;padding-left:19px;border-radius:3px 3px 0 0;display:flex;align-items:center;gap:8px}
.feed-head .mark{width:13px;height:13px;border-radius:50%;background:var(--white)}
.tweet{display:flex;gap:7px;padding:0 10px 0 15px;margin-top:12px}
.tweet-avatar{flex:none;width:39px;height:39px;border-radius:3px;background:linear-gradient(160deg,#e4c27e,#c79b5a 60%,#8a6a48)}
.tweet-body{font-size:8.6px;line-height:14.4px;color:#666}
.tweet-body b{font-weight:600;color:#333;font-size:9.4px}
.tweet-actions{margin-top:4px;color:#444;font-size:9px}
.gallery-title{position:absolute;top:845px;font-size:22px;font-weight:400}
.photo-title{left:46px;color:var(--pink)}
.video-title{left:487px;color:var(--purple)}
.thumb{position:absolute;width:131px;height:100px;border:1px solid #ddd}
.vthumb{position:absolute;width:183px;height:103px}
.play{position:absolute;left:50%;top:50%;width:28px;height:28px;margin:-14px 0 0 -14px}
.footer{position:absolute;left:0;top:1142px;width:910px;height:58px;background:var(--pink);color:var(--white)}
.footer-copy{position:absolute;left:47px;top:21px;font-size:11px}
.social{position:absolute;right:73px;top:14px;display:flex;gap:4px}
.social span{width:26px;height:26px;border-radius:50%;background:var(--white)}
</style>
</head>
<body>
<div class="top-stripe"></div>

<header class="brand">
  <div class="brand-name"><span class="first">Miriam</span> <span class="last">Halvorsen</span></div>
  <div class="brand-slogan">Your Slogan goes here</div>
</header>

<nav class="main-nav">
  <a>HOME</a><a>BIOGRAPAHIE</a><a>INTERVIEW</a><a>PRIVATE PHOTOS</a><a>EROTIC PHOTOS</a><a>AUTOGRAMME</a><a>CHARITY</a><a>CONTACT</a>
</nav>

<section class="hero" role="img" aria-label="Portrait photo of the actress smiling outdoors beside a tree">
  <div class="hero-fade"></div>
  <div class="hero-text">
    <div class="hero-kicker">PHASELLUS FELIS DOLOR</div>
    <div class="hero-title">SCELERISQUE TEMPUS</div>
    <p class="hero-copy">Etiam eu urna Sed porta Suspendisse quam leo molestie sed luctus quis feugiat in pede Fusce tellus Sed metus augue convallis</p>
    <div class="dots"><span class="active"></span><span></span><span></span><span></span></div>
  </div>
</section>

<section class="intro">
  <h1>Malesuada nec ultricies sit amet porttitor</h1>
  <h2>Aliquam nec erat at purus cursus interdum</h2>
  <p>Nascetur ridiculus mus In iaculis facilisis massa Etiam eu urna Sed porta Suspendisse quam leo molestie sed luctus quis feugiat in pede Fusce tellus Sed metus augue convallis et vehicula ut pulvinar eu ante Integer orci tellus tristique vitae consequat nec porta vel lectus Nulla sit amet diam Duis non nunc</p>
  <p>libero a tempus libero lectus feugiat felis Morbi diam mauris viverra in gravida eu mattis in ante Morbi eget arcu Morbi porta libero id ullamcorper nonummy nibh ligula pulvinar metus eget consv et scelerisque mi tortor at ipsum Maecenas at justo id velit placerat molestie Donec dictum lectus non odio Cras a ante vitae enim iaculis aliquam Mauris nunc quam venenatis nec euismod sit amet egestas placerat est</p>
  <p>Pellentesque habitant morbi tristique senectus et netus et malesuada fames ac turpis egestas Cras id elit Integer quis urna Ut ante enim dapibus malesuada fringilla eu condimentum quis tellus Aenean porttitor eros vel dolor Donec convallis pede venenatis nibh Duis quam</p>
</section>

<aside class="feed">
  <div class="feed-head">Chatter Feed <span class="mark"></span></div>
  <div class="tweet">
    <div class="tweet-avatar" role="img" aria-label="Profile picture"></div>
    <div class="tweet-body"><b>Miriam Halvorsen</b> @MirHalvorsen<br>Ich habe heute abend ein #date mit<br>meinem TV. Die Kollegen vom
      <div class="tweet-actions">Reply &nbsp;|&nbsp; Retweet &nbsp;|&nbsp; Favorite</div></div>
  </div>
  <div class="tweet">
    <div class="tweet-avatar" role="img" aria-label="Profile picture"></div>
    <div class="tweet-body"><b>Miriam Halvorsen</b> @MirHalvorsen<br>"@RadlerinLena: eigene PR: Ich suche<br>einen Social-Media Job. Be my Boss!<br>http://jobblick.de/be-my-boss/ #deinjob"
      <div class="tweet-actions">Reply &nbsp;|&nbsp; Retweet &nbsp;|&nbsp; Favorite</div></div>
  </div>
  <div class="tweet">
    <div class="tweet-avatar" role="img" aria-label="Profile picture"></div>
    <div class="tweet-body"><b>Miriam Halvorsen</b> @MirHalvorsen<br>"@abendnachricht: Katar: Hunderte<br>Tote beim Stadionbau für die WM?<br>http://kurz.ly/4hx2pa #Katar
      <div class="tweet-actions">Reply &nbsp;|&nbsp; Retweet &nbsp;|&nbsp; Favorite</div></div>
  </div>
</aside>

<h3 class="gallery-title photo-title">PHOTO GALLERY</h3>
<div class="thumb" style="left:47px;top:885px;background:linear-gradient(135deg,#e9e9ee,#7a4a30 60%,#3a2a22)" role="img" aria-label="Gallery photo: actress at an event"></div>
<div class="thumb" style="left:188px;top:885px;background:linear-gradient(135deg,#3a1c18,#d9b07a 50%,#b3242a)" role="img" aria-label="Gallery photo: actress portrait"></div>
<div class="thumb" style="left:329px;top:885px;background:linear-gradient(135deg,#7a5e48,#e6c89a 50%,#5a4636)" role="img" aria-label="Gallery photo: smiling portrait"></div>
<div class="thumb" style="left:47px;top:995px;background:linear-gradient(135deg,#5a4a3e,#d7b68a 55%,#9a7e60)" role="img" aria-label="Gallery photo: portrait"></div>
<div class="thumb" style="left:188px;top:995px;background:linear-gradient(135deg,#e3ecf4,#b69070 50%,#f0f2f6)" role="img" aria-label="Gallery photo: portrait with wavy hair"></div>
<div class="thumb" style="left:329px;top:995px;background:linear-gradient(135deg,#6a4a2a,#d8a458 55%,#8a6436)" role="img" aria-label="Gallery photo: laughing portrait"></div>

<h3 class="gallery-title video-title">VIDEO GALLERY</h3>
<div class="vthumb" style="left:491px;top:881px;background:linear-gradient(160deg,#b9c7d6,#5e7e86 55%,#9fb0be)" role="img" aria-label="Video still: actress on stage">
  <svg class="play" viewBox="0 0 28 28"><circle cx="14" cy="14" r="13" fill="#fff"/><circle cx="14" cy="14" r="11" fill="#222"/><path d="M11 9l8 5-8 5z" fill="#fff"/></svg></div>
<div class="vthumb" style="left:681px;top:881px;background:linear-gradient(90deg,#8a3a1a,#c9823a 45%,#e0b060)" role="img" aria-label="Video still: interview">
  <svg class="play" viewBox="0 0 28 28"><circle cx="14" cy="14" r="13" fill="#fff"/><circle cx="14" cy="14" r="11" fill="#222"/><path d="M11 9l8 5-8 5z" fill="#fff"/></svg></div>
<div class="vthumb" style="left:491px;top:992px;background:linear-gradient(90deg,#6a1a1a,#c9b090 50%,#7a2020)" role="img" aria-label="Video still: award show">
  <svg class="play" viewBox="0 0 28 28"><circle cx="14" cy="14" r="13" fill="#fff"/><circle cx="14" cy="14" r="11" fill="#222"/><path d="M11 9l8 5-8 5z" fill="#fff"/></svg></div>
<div class="vthumb" style="left:681px;top:992px;background:linear-gradient(90deg,#9aa4ae,#d9c08a 50%,#5a6472)" role="img" aria-label="Video still: press event">
  <svg class="play" viewBox="0 0 28 28"><circle cx="14" cy="14" r="13" fill="#fff"/><circle cx="14" cy="14" r="11" fill="#222"/><path d="M11 9l8 5-8 5z" fill="#fff"/></svg></div>

<footer class="footer">
  <div class="footer-copy">© 2014 Company Name. &nbsp;All right reserved. &nbsp;Term of Use</div>
  <div class="social"><span></span><span></span><span></span><span></span></div>
</footer>
</body>
</html>
```